Celvara Health Group Presentation Folder, for Cancer Awareness, VERY COLORFUL AND MODERN

Presentation Folder I know pretty much what i want so it should be very eazy , I have included files from folders I use now rebrand them to my new company they will be fine, no sense re creating the wheel
Full Bleed Size
20.87" x 16.68"
53 x 42.4 cm
6260 x 5004 pixels
Document Trim Size
20.75" x 16.56"
52.7 x 42.1 cm
6225 x 4969 pixels

Low design quality

Industry/Entity Type

Medical

Font styles to use
Serif

Colors

Designer to choose colors to be used in the design.

Requirements
Must have
• really I am not looking for some one to redesign, we like our folder front page and would like to see new word information added., there are two folder front pages to choose from
• So Keep the original front page and redesign the back page and the pockets
• Can Make your Design off of one of the ones I already uploaded
Nice to have
• Keep the same color schemes, Keep the original front page and redesign the back page and the pockets
Should not have
• DO not recreate the front covers, use what I gave you and just rebrand

```html
<!DOCTYPE html>
<html lang="en">
<head>
<meta charset="utf-8">
<title>Celvara Health Group – Presentation Folder</title>
<link href="https://fonts.googleapis.com/css2?family=Raleway:wght@300;400;500;700&display=swap" rel="stylesheet">
<style>
:root{
  --stage:#7f7f7f;
  --paper:#ffffff;
  --navy:#2a2743;
  --navy-deep:#1f1c36;
  --band:#4b4b53;
  --tag:#7c7c82;
  --ink:#222233;
  --body:#555560;
  --sheen:#e4e4e6;
}
*{margin:0;padding:0;box-sizing:border-box}
html,body{width:1200px;height:1200px;overflow:hidden;background:var(--stage);font-family:"Raleway",sans-serif}
.spread{position:absolute;background:var(--paper)}
.spread--outer{left:137px;top:86px;width:694px;height:473px}
.spread--inner{left:342px;top:626px;width:692px;height:464px}
.panel-right{position:absolute;top:0;bottom:0;left:346px;right:0;background:linear-gradient(90deg,var(--sheen) 0%,#f7f7f8 30%,#fff 60%)}

/* back cover */
.collage{position:absolute;left:27px;top:45px;width:294px;height:232px;background:var(--navy);padding:2px;display:grid;gap:2px;
  grid-template-columns:repeat(12,1fr);grid-template-rows:74px 87px 1fr}
.collage .photo{border-radius:0}
.p1{grid-column:1/6;background:linear-gradient(180deg,#b9cde6,#8a8f7a)}
.p2{grid-column:6/13;background:linear-gradient(180deg,#9bbf6a,#e2d6c4)}
.p3{grid-column:1/6;background:linear-gradient(180deg,#e6d6c8,#c98b7a)}
.p4{grid-column:6/13;background:linear-gradient(180deg,#5fa4e0,#e8e2d2)}
.p5{grid-column:1/6;background:linear-gradient(180deg,#d8c3a6,#b48b66)}
.p6{grid-column:6/13;background:linear-gradient(180deg,#6e9e5a,#d77a3a 60%,#6bbf5a)}
.back-copy{position:absolute;left:27px;top:293px;width:294px;font-size:6.6px;line-height:1.3;color:var(--ink);text-align:justify}
.back-quote{position:absolute;left:27px;top:339px;width:294px;font-size:10px;line-height:1.25;font-weight:700;color:var(--navy);text-align:justify}
.footer-band{position:absolute;left:0;right:0;top:395px;height:27px;background:var(--band)}
.directions{position:absolute;left:23px;top:9px;font-size:6px;color:#fff}
.cover-tagline{position:absolute;left:346px;right:0;top:8px;text-align:center;font-size:10px;font-weight:300;color:#fff}

/* front cover */
.title-bar{position:absolute;left:346px;top:44px;width:348px;height:32px;background:var(--navy);color:#fff;font-weight:300;font-size:20px;letter-spacing:.2px;line-height:32px;text-align:center}
.gatekeeper{position:absolute;left:407px;top:78px;width:218px;height:20px;background:var(--tag);color:#fff;font-size:7.5px;font-weight:300;line-height:20px;text-align:center}
.obligation{position:absolute;left:346px;right:0;top:102px;text-align:center;font-size:10px;font-weight:300;line-height:1.2;color:var(--ink)}
.cover-photo{position:absolute;left:346px;top:140px;width:348px;height:241px;background:linear-gradient(160deg,#f4efe6 0%,#d9c3a6 45%,#9b8c7a 100%)}
.cover-mark{position:absolute;left:372px;top:428px;display:flex;align-items:center;gap:5px}
.cover-mark .dot{width:30px;height:30px;border-radius:50%;background:var(--navy);border:3px solid #fff}
.cover-mark span{font-size:7px;font-weight:700;color:var(--navy)}

/* inside */
.inside-copy{position:absolute;left:394px;width:236px;font-size:7.2px;line-height:1.42;font-weight:300;color:var(--body);text-align:justify}
.inside-copy.one{top:184px}
.inside-copy.two{top:285px}
.inside-claim{position:absolute;left:394px;top:354px;width:236px;font-size:10.5px;line-height:1.45;color:#111;text-align:justify;font-weight:500}
.pockets{position:absolute;left:0;top:318px}
.pocket-brand{position:absolute;left:441px;top:352px;display:flex;align-items:center;gap:8px}
.pocket-brand .dot{width:56px;height:56px;border-radius:50%;background:#fff}
.pocket-brand .rule{width:1px;height:60px;background:#fff}
.pocket-brand .name{color:#fff;font-weight:700;font-size:18px;line-height:1;text-transform:uppercase;letter-spacing:.5px}
.division{position:absolute;left:380px;width:300px;top:427px;text-align:center;color:#fff;font-size:8px;font-weight:300}
</style>
</head>
<body>

<section class="spread spread--outer">
  <div class="panel-right"></div>

  <div class="collage">
    <div class="photo p1" role="img" aria-label="Family walking together outdoors"></div>
    <div class="photo p2" role="img" aria-label="Family lying on the grass"></div>
    <div class="photo p3" role="img" aria-label="Three generations of a family at home"></div>
    <div class="photo p4" role="img" aria-label="Family holding hands on a beach"></div>
    <div class="photo p5" role="img" aria-label="Family portrait on a sofa"></div>
    <div class="photo p6" role="img" aria-label="Large family reunion group on a lawn"></div>
  </div>

  <p class="back-copy">Hereditary cancer screening provides vital information to help people with a strong personal or family history of cancer understand their own risk of developing the disease. With this information, they can take steps to Potentially Prevent Cancer, Delay the Onset of Cancer or Catch it at an Earlier stage when outcomes and survival rates are Better.</p>
  <p class="back-quote">Don’t be Afraid of the Answer: Knowledge is Power and Power Eradicates Fear. When You are Fearless, You Will Make all the Right Choices!</p>

  <h1 class="title-bar">HEREDITARY CANCER SCREENING</h1>
  <p class="gatekeeper">Doctors are the Gatekeepers to Genetic Testing.</p>
  <p class="obligation">We have an obligation to help patients understand genetic<br>risk and how testing can guide heath care decisions.</p>
  <div class="cover-photo" role="img" aria-label="Multi-generation family sharing a meal at an outdoor table"></div>

  <div class="footer-band">
    <p class="directions">Directions – USE any family picture I provided AND THE WORDS -Use you creativity to make it nice</p>
    <p class="cover-tagline">The test you order FOR your patients</p>
  </div>
  <div class="cover-mark"><div class="dot"></div><span>Celvara Health Group</span></div>
</section>

<section class="spread spread--inner">
  <div class="panel-right"></div>

  <p class="inside-copy one" style="top:61px">There are many benefits to getting tested, regardless of the eventual result. If one of your family members — however distant — had cancer, there is a chance that you inherited a gene mutation that not only increases your personal risk of cancer, but also could be passed to the next generation. Those who are carriers of hereditary cancer gene mutations could be at risk of getting cancer earlier in life than the general population. The sooner genetic testing is done the more likely it is that the risk can be managed appropriately.</p>
  <p class="inside-copy two" style="top:162px">Hereditary cancer screening provides vital information to help people with a strong personal or family history of cancer understand their own risk of developing the disease. With this information, they can take steps to Potentially Prevent Cancer, Delay the Onset of Cancer or Catch it at an Earlier stage when outcomes and survival rates are Better.</p>
  <p class="inside-claim" style="top:232px">Identifying an inherited genetic mutation has the potential to prevent cancer and save lives.</p>

  <svg class="pockets" width="692" height="146" viewBox="0 0 692 146" aria-hidden="true">
    <defs>
      <linearGradient id="pocketFill" x1="0" y1="0" x2="0" y2="1">
        <stop offset="0" stop-color="#2c2947"/>
        <stop offset="1" stop-color="#1f1c36"/>
      </linearGradient>
    </defs>
    <path d="M0 0 H314 Q326 0 328 12 L345 146 H0 Z" fill="url(#pocketFill)"/>
    <path d="M692 0 H376 Q364 0 362 12 L347 146 H692 Z" fill="url(#pocketFill)"/>
    <g stroke="#16142a" stroke-width="1.2" opacity=".7">
      <line x1="113" y1="27" x2="140" y2="13"/>
      <line x1="208" y1="13" x2="235" y2="27"/>
      <line x1="113" y1="110" x2="140" y2="124"/>
      <line x1="208" y1="124" x2="235" y2="110"/>
    </g>
  </svg>

  <div class="pocket-brand">
    <div class="dot"></div>
    <div class="rule"></div>
    <div class="name">Celvara<br>Health<br>Group</div>
  </div>
  <p class="division">a division of Meridane Medical Sales LLC</p>
</section>

</body>
</html>
```